App-Design für Vergleichsportal für Reparaturen
Zielgruppe
Flickwerkzentrale ist das Vergleichsportal für Reparaturen in deiner Nähe. Egal ob du eine Werkstatt für dein Smartphone, Tablet, Laptop, Computer, Smartwatch oder Spielkonsole suchst. Mit uns findest du deine passende Reparaturwerkstat in deiner Nähe mit dem besten Preis für dich. Du kannst dich direkt über unser Portal deinen Reparaturauftrag erhalten und wirst durch unser Sicher Kaufen Käuferschutz und unser VORMANT Treuhandschutz abgesichert.
Aufgabenstellung
Unter Flickwerkzentrale.de kann das aktuelle Design angeschaut werden. Die Farbe sollten übernommen werden.
Über die Startseite kann der Kunde sein Gerät, Service sowie seine Adresse eingeben. Auf der Vergleichsseite bekommt der Kunde die Übersicht welche Reparaturwerkstätten es gibt, zu welche Preisen die ausgewählte Dienstleistung angeboten wird. Wenn der Kunde auf den Button 'Jetzt Online Bestpreis buchen' drückt, dann kommt der Kunde in den Warenkorb. Im Warenkorb können noch weitere Dienstleistungen und Produkte dazugebucht werden. Und anschließend kommt der Kunde in die Kasse und kann der Bestellvorgang beenden. Die Benutzerführung sollte einfach sein. Im Fokus steht die Vergleichsseite. Dort sollte der Kunde ca. 4 Werkstätten auf einen Blick sehen können. Könnte ausschauen wie bei Tarifblick in der Kategorie Mobilfunk.
Die Vergleichseite sollte auf jeden Fall folgende Elemente enthalten:
- Entfernung zur Werkstatt in Meter bzw. Kilometer
- Logo der Werkstatt
- Name der Werkstatt
- Bewertungssterne der Werkstatt
- Reparaturzeit und Ersatzeilverfügbarkeit
- Reparaturpreis (Platz sollte auch bei Auswahl von 2 Dienstleistungen vorhanden sein)
- Rabattanzeige
- Qualitätssiegel (noch nicht vorhanden)
- Anzeige von Verknappung (z. B. noch 3 Termin frei)
- Qualitätsmerkmale (z. B. 12 Monate Garantie)
Die Merkmale Öffnungszeiten, Adresse, Kostenpflichtige Zusatzleistungen können aus Platzgründen in den Warenkorbseite wandern außer es gibt eine schöne und einfache Lösung.
In der Warenkorbseite kann dazu auch die Tarifblick Seite dienen.
Bei allen sollte auf die Benutzerfreundlichkeit geachtet werden.
Bei offenen Frage stehe ich zur Verfügung und freue mich auf viele Designs.
Vielen DANK im Voraus!

```html
<!DOCTYPE html>
<html lang="de">
<head>
<meta charset="utf-8">
<title>Flickwerkzentrale – App-Screens</title>
<link href="https://fonts.googleapis.com/css2?family=Roboto:wght@400;500;700&display=swap" rel="stylesheet">
<style>
:root{
  --green:#8cc63f;
  --teal:#1f4a5f;
  --ink:#1e1e1e;
  --muted:#8a8a8a;
  --line:#e3e3e3;
  --page:#f7f7f7;
  --link:#5a7fd6;
}
*{box-sizing:border-box;margin:0;padding:0}
html,body{width:1200px;height:959px;overflow:hidden;background:var(--page);font-family:"Roboto",Arial,sans-serif;color:var(--ink)}
.stage{position:absolute;left:0;top:0;width:1425px;height:1139px;transform:scale(.8421);transform-origin:0 0}
.phone{position:absolute;width:278px;height:496px;background:#fff;box-shadow:0 1px 3px rgba(0,0,0,.25);overflow:hidden}
.abs{position:absolute}
.center{position:absolute;left:0;right:0;text-align:center}
.status{position:absolute;left:0;right:0;top:0;height:16px;font-size:7.5px}
.status .carrier{position:absolute;left:4px;top:4px}
.status .time{position:absolute;left:0;right:0;top:4px;text-align:center}
.status .batt{position:absolute;right:4px;top:4px;display:flex;align-items:center;gap:2px}
.status .batt i{display:inline-block;width:17px;height:6px;background:#111;border-radius:1px}
.head{position:absolute;left:0;right:0;top:0;height:60px;background:#fff;box-shadow:0 1px 3px rgba(0,0,0,.08);z-index:2}
.brand{position:absolute;left:0;right:0;top:31px;text-align:center;font-size:10px;font-weight:500;color:var(--green)}
.brand::before{content:"";display:inline-block;width:7px;height:7px;border-radius:50%;background:var(--green);margin-right:3px;vertical-align:0}
.back{position:absolute;left:9px;top:33px}
.basket{position:absolute;right:12px;top:30px}
.label{font-size:7px;font-weight:500;position:absolute;left:0;right:0;text-align:center}
.cat{position:absolute;top:103px;width:101px;height:77px;border:1px solid #e8e8e8;background:#fff;font-size:8.5px;text-align:center}
.cat.on{background:var(--green);border-color:var(--green);color:#fff;font-weight:700}
.cat span{position:absolute;left:0;right:0;top:59px}
.cat svg{position:absolute;left:50%;top:12px;transform:translateX(-50%)}
.dots{position:absolute;left:0;right:0;text-align:center;font-size:6px;color:#aaa;letter-spacing:3px}
.field{position:absolute;left:17px;width:239px;height:37px;border:1px solid #ddd;font-size:9.5px;color:var(--muted);padding:12px 14px;box-shadow:0 1px 2px rgba(0,0,0,.05)}
.field.dark{border-color:#999;color:var(--ink)}
.field .chev{position:absolute;right:9px;top:11px;font-size:10px}
.btn{position:absolute;left:17px;width:241px;height:36px;background:var(--teal);color:#fff;font-size:9.5px;text-align:center;line-height:36px;border-radius:2px;box-shadow:0 1px 3px rgba(0,0,0,.3);letter-spacing:.2px}
.loc{position:absolute;left:17px;width:226px;height:22px;border:1px solid #e4e4e4;font-size:8.5px;line-height:20px;padding-left:15px;white-space:nowrap;overflow:hidden}
.loc b{font-weight:700;font-size:7.5px}
.loc small{font-size:5px;margin-right:8px}
.row{position:absolute;left:0;right:0;height:34px;border-bottom:1px solid var(--line);font-size:9px}
.row .x{position:absolute;left:31px;top:12px;color:#aaa;font-size:8px}
.row .name{position:absolute;left:49px;top:11px}
.row .price{position:absolute;right:24px;top:11px;font-weight:700}
.slot{position:absolute;width:59px;height:29px;border:1px solid #e3e3e3;font-size:9.5px;color:#555;text-align:center;line-height:27px}
.slot.on{background:var(--green);border-color:var(--green);color:#fff}
.total{position:absolute;left:0;right:0;height:21px;background:var(--green);color:#fff;font-size:8px;font-weight:700;line-height:21px}
.pay{position:absolute;top:250px;height:22px;border:1px solid #ccc;font-size:9px;font-weight:700;color:var(--teal);text-align:center;line-height:20px}
.extra{position:absolute;left:17px;width:223px;height:22px;border:1px solid #ddd;font-size:9px;line-height:20px;padding-left:28px}
.extra svg{position:absolute;left:12px;top:6px}
.info{position:absolute;left:249px;width:9px;height:9px;border-radius:50%;background:#ccc;color:#fff;font-size:6px;text-align:center;line-height:9px}
.phone-ico{color:var(--green);font-size:7px;margin-right:4px}
</style>
</head>
<body>
<div class="stage">

<svg width="0" height="0" style="position:absolute">
  <defs>
    <symbol id="basket" viewBox="0 0 14 14"><path d="M1 5h12l-1.5 7h-9z M4 5l3-4 3 4" fill="none" stroke="#111" stroke-width="1.4" stroke-linejoin="round"/></symbol>
    <symbol id="back" viewBox="0 0 8 12"><path d="M6 1L2 6l4 5" fill="none" stroke="#111" stroke-width="1.5"/></symbol>
  </defs>
</svg>

<!-- Splash -->
<section class="phone" style="left:70px;top:40px">
  <div class="status"><span class="carrier">●●●●● Netz</span><span class="time">9:41 AM</span><span class="batt">100% <i></i></span></div>
  <div class="center" style="top:162px;font-size:27px;font-weight:500;color:var(--teal)"><span style="display:inline-block;width:20px;height:20px;border-radius:50%;background:var(--green);margin-right:6px;vertical-align:-2px"></span>Flickwerkzentrale</div>
  <div class="center" style="top:388px;font-size:11.5px;font-weight:700;line-height:16px">DAS VERGLEICHSPORTAL FÜR<br>REPARATUREN IN DEINER NÄHE</div>
  <div class="abs" style="left:0;right:0;top:481px;height:15px;background:#e9e9e9;font-size:5px;color:#999;text-align:center;line-height:15px">Datenschutz</div>
</section>

<!-- Kategorie -->
<section class="phone" style="left:389px;top:40px">
  <header class="head">
    <div class="status"><span class="carrier">●●●●● Netz</span><span class="time">9:41 AM</span><span class="batt">100% <i></i></span></div>
    <div class="brand">Flickwerkzentrale</div>
    <svg class="basket" width="14" height="14"><use href="#basket"/></svg>
  </header>
  <div class="label" style="top:84px">Bitte wählen Sie die Reparaturkategorie</div>
  <div class="cat" style="left:-88px"><span style="left:auto;right:12px">Tablet</span><svg width="20" height="34" style="left:auto;right:-6px;transform:none"><rect x="1" y="1" width="14" height="32" rx="2" fill="none" stroke="#111" stroke-width="2"/></svg></div>
  <div class="cat on" style="left:32px"><svg width="30" height="40"><rect x="2" y="2" width="26" height="36" rx="3" fill="none" stroke="#fff" stroke-width="2.5"/><line x1="12" y1="32" x2="18" y2="32" stroke="#fff" stroke-width="2"/></svg><span>Tablet</span></div>
  <div class="cat" style="left:140px"><svg width="48" height="34" style="top:16px"><rect x="4" y="2" width="40" height="24" fill="none" stroke="#111" stroke-width="2"/><line x1="0" y1="31" x2="48" y2="31" stroke="#111" stroke-width="2"/></svg><span>Laptop</span></div>
  <div class="cat" style="left:247px"><svg width="30" height="34" style="left:12px;transform:none;top:16px"><rect x="2" y="2" width="30" height="24" fill="none" stroke="#111" stroke-width="2"/></svg><span style="left:14px;text-align:left">Laptop</span></div>
  <div class="dots" style="top:186px">• • • •</div>
  <div class="field" style="top:208px">Hersteller wählen<span class="chev">›</span></div>
  <div class="field" style="top:252px">Dienstleistung wählen<span class="chev">›</span></div>
  <div class="label" style="top:318px">Geben Sie Ihre Agresse ein</div>
  <div class="field dark" style="top:337px">Strasse</div>
  <div class="field dark" style="top:380px">Haus Nummer</div>
  <div class="btn" style="top:438px">LOS</div>
</section>

<!-- Gerät -->
<section class="phone" style="left:711px;top:40px">
  <header class="head">
    <div class="status"><span class="carrier">●●●●● Netz</span><span class="time">9:41 AM</span><span class="batt">100% <i></i></span></div>
    <svg class="back" width="8" height="12"><use href="#back"/></svg>
    <div class="brand">Flickwerkzentrale</div>
    <svg class="basket" width="14" height="14"><use href="#basket"/></svg>
  </header>
  <div class="label" style="top:84px">Gerät wählen</div>
  <div class="cat" style="left:-74px"><span style="left:auto;right:-2px;width:16px;text-align:left">5</span></div>
  <div class="cat on" style="left:32px"><svg width="30" height="40"><rect x="2" y="2" width="26" height="36" rx="3" fill="none" stroke="#fff" stroke-width="2.5"/><line x1="12" y1="32" x2="18" y2="32" stroke="#fff" stroke-width="2"/></svg><span>Tab Pro 2 12,9</span></div>
  <div class="cat" style="left:141px"><svg width="30" height="40"><rect x="2" y="2" width="26" height="36" rx="3" fill="none" stroke="#111" stroke-width="2.5"/><line x1="12" y1="32" x2="18" y2="32" stroke="#111" stroke-width="2"/></svg><span>Tab Pro 10,5</span></div>
  <div class="cat" style="left:248px"><span style="left:26px;text-align:left">5</span></div>
  <div class="dots" style="top:182px">• • • •</div>
  <div class="field dark" style="top:207px;left:17px;width:238px">Dienstleistung wählen<span class="chev">›</span></div>
  <div class="label" style="top:273px;font-size:6.5px">Standorte in der Nähe</div>
  <div class="loc" style="top:293px"><b>100</b> <small>m.</small>Ahornweg 14, 10115 Musterstadt</div>
  <div class="loc" style="top:319px"><b>2</b> <small>km.</small>Ahornweg 14, Musterstadt</div>
  <div class="loc" style="top:344px"><b>13</b> <small>km.</small>Lindenallee 12, 80331 Musters…</div>
  <div class="loc" style="top:370px"><b>100</b> <small>m.</small>Ahornweg 14, 10115 Musterstadt</div>
  <div class="loc" style="top:395px"><b>100</b> <small>m.</small>Lindenallee 12, 80331 Musters…</div>
  <div class="abs" style="left:253px;top:293px;width:2px;height:21px;background:var(--teal)"></div>
  <div class="abs" style="left:253px;top:314px;width:1px;height:103px;background:#e3e3e3"></div>
  <div class="btn" style="top:438px">LOS</div>
</section>

<!-- Werkstatt -->
<section class="phone" style="left:1042px;top:40px;background:#f5f5f5">
  <header class="head">
    <div class="status"><span class="carrier">●●●●● Netz</span><span class="time">9:41 AM</span><span class="batt">100% <i></i></span></div>
    <svg class="back" width="8" height="12"><use href="#back"/></svg>
    <div class="brand">Flickwerkzentrale</div>
    <svg class="basket" width="14" height="14"><use href="#basket"/></svg>
  </header>
  <div class="abs" style="left:0;right:0;top:60px;height:290px;background:#fff;box-shadow:0 1px 3px rgba(0,0,0,.08)"></div>
  <div class="abs" style="left:32px;top:93px;font-size:8px;font-weight:700;color:var(--green)">Geräteklinik.de</div>
  <div class="abs" style="left:32px;top:110px;font-size:23px;font-weight:700;line-height:27px">Geräteklinik<br>Sicher Kaufen</div>
  <div class="abs" style="left:32px;top:182px;font-size:8.5px;line-height:14px">Lindenallee 12<br>80331 Musterstadt</div>
  <div class="abs" style="left:163px;top:182px;font-size:8px;line-height:15px"><span class="phone-ico">✆</span>01234 - 5670 111<br><span class="phone-ico">✆</span>01234 - 5674 125</div>
  <div class="abs" style="left:32px;top:217px;font-size:8.5px;line-height:14px">Öffnungszeiten:<br>Mo-Fr. 9.00 Uhr - 18.00 Uhr<br>Sa. 10.00 Uhr - 15.00 Uhr</div>
  <div class="abs" style="left:0;right:0;top:277px;height:73px;border-top:1px solid #eee"></div>
  <div class="abs" style="left:45px;top:287px;font-size:29px;font-weight:700">150<span style="font-size:16px;font-weight:500">m.</span></div>
  <div class="abs" style="left:47px;top:322px;font-size:12px;color:var(--green);letter-spacing:1px">★★★★<span style="color:#ccc">★</span></div>
  <div class="abs" style="left:148px;top:290px;width:1px;height:46px;background:#eee"></div>
  <svg class="abs" style="left:195px;top:290px" width="24" height="24"><rect x="1.5" y="3.5" width="21" height="19" fill="none" stroke="#111" stroke-width="1.5"/><line x1="1.5" y1="8" x2="22.5" y2="8" stroke="#111" stroke-width="2"/><line x1="7" y1="1" x2="7" y2="5" stroke="#111" stroke-width="1.5"/><line x1="17" y1="1" x2="17" y2="5" stroke="#111" stroke-width="1.5"/><text x="12" y="19" font-size="9" font-weight="700" text-anchor="middle" font-family="Roboto,Arial,sans-serif">19</text></svg>
  <div class="abs" style="left:178px;top:323px;font-size:5.5px;color:var(--link)">noch <span style="font-size:8px;color:var(--ink)">3</span> Termin frei</div>
  <div class="row" style="top:350px;background:#fff"><span class="x">✕</span><span class="name">Bluetooth Antenne</span><span class="abs" style="left:183px;top:13px;font-size:5.5px;color:var(--link)">200€ -50%</span><span class="price">100 €</span></div>
  <div class="row" style="top:384px;background:#fff"><span class="x">✕</span><span class="name">SIM Lesemodul</span><span class="price">100 €</span></div>
  <div class="btn" style="top:438px">JETZT ONLINE BESTPREIS BUCHEN</div>
</section>

<!-- Termine -->
<section class="phone" style="left:389px;top:585px">
  <header class="head">
    <div class="status"><span class="carrier">●●●●● Netz</span><span class="time">9:41 AM</span><span class="batt">100% <i></i></span></div>
    <svg class="back" width="8" height="12"><use href="#back"/></svg>
    <div class="brand">Flickwerkzentrale</div>
    <svg class="basket" width="14" height="14"><use href="#basket"/></svg>
  </header>
  <div class="abs" style="left:15px;top:82px;width:245px;height:328px;background:#fff;box-shadow:0 1px 4px rgba(0,0,0,.2)">
    <div class="abs" style="left:19px;top:18px;font-size:10px;font-weight:700">Nächste Termine</div>
    <div class="abs" style="left:220px;top:14px;font-size:13px;color:#bbb">✕</div>
    <div class="abs" style="left:19px;top:47px;font-size:8.5px">AUG 17</div>
    <div class="slot on" style="left:19px;top:66px">11 AM</div>
    <div class="slot" style="left:90px;top:66px">1 PM</div>
    <div class="slot" style="left:162px;top:66px">3 PM</div>
    <div class="slot" style="left:19px;top:108px">4 PM</div>
    <div class="slot" style="left:90px;top:108px">11 AM</div>
    <div class="abs" style="left:19px;top:155px;font-size:8.5px">AUG 19</div>
    <div class="slot" style="left:19px;top:174px">10 AM</div>
    <div class="slot" style="left:90px;top:174px">11 AM</div>
    <div class="abs" style="left:17px;top:230px;font-size:8.5px;text-decoration:underline">SHOW CALENDAR</div>
    <div class="btn" style="left:17px;top:272px;width:211px;height:35px;line-height:35px">TERMIN BUCHEN</div>
  </div>
  <div class="btn" style="top:437px">JETZT ONLINE BESTPREIS BUCHEN</div>
</section>

<!-- Warenkorb -->
<section class="phone" style="left:711px;top:585px">
  <header class="head">
    <div class="status"><span class="carrier">●●●●● Netz</span><span class="time">9:41 AM</span><span class="batt">100% <i></i></span></div>
    <svg class="back" width="8" height="12"><use href="#back"/></svg>
    <div class="brand">Flickwerkzentrale</div>
    <svg class="basket" width="14" height="14"><use href="#basket"/></svg>
  </header>
  <div class="center" style="top:82px;font-size:21px;font-weight:700">Warenkorb</div>
  <div class="abs" style="left:0;right:0;top:118px;border-top:1px solid var(--line)"></div>
  <div class="abs" style="left:32px;top:129px;font-size:7.5px;color:var(--muted)">Leistung</div>
  <div class="abs" style="right:28px;top:129px;font-size:7.5px;color:var(--muted)">Preis</div>
  <div class="row" style="top:147px;border-top:1px solid var(--line)"><span class="x" style="left:12px">✕</span><span class="name" style="left:32px">Bluetooth Antenne</span><span class="price">100 €</span></div>
  <div class="row" style="top:181px"><span class="x" style="left:12px">✕</span><span class="name" style="left:32px">SIM Lesemodul</span><span class="price">100 €</span></div>
  <div class="abs" style="left:200px;top:118px;width:1px;height:97px;background:var(--line)"></div>
  <div class="total" style="top:215px"><span style="margin-left:32px">Total</span><span class="abs" style="right:24px">200 €</span></div>
  <div class="abs" style="left:32px;top:255px;font-size:9px;color:#444">Zahlungsmethoden:</div>
  <div class="pay" style="left:154px;width:41px">Kartenpay</div>
  <div class="pay" style="left:201px;width:57px">Netzpay</div>
  <div class="btn" style="top:295px;height:35px;line-height:35px">ZUR KASSE</div>
  <div class="label" style="top:356px;font-size:6.5px">Passende Leistungen</div>
  <div class="extra" style="top:375px"><svg width="6" height="8"><path d="M3 8C1 5 0 4 0 3a3 3 0 016 0c0 1-1 2-3 5z" fill="#111"/></svg>W-LAN Antenne</div>
  <div class="extra" style="top:400px"><svg width="6" height="8"><circle cx="3" cy="4" r="2.5" fill="#111"/></svg>Bluetooth Antenne</div>
  <div class="extra" style="top:425px"><svg width="8" height="7"><path d="M0 2a6 6 0 018 0M1.5 4a4 4 0 015 0" fill="none" stroke="#111" stroke-width="1"/><circle cx="4" cy="6" r="1" fill="#111"/></svg>GPS Antenne</div>
  <div class="extra" style="top:450px"><svg width="8" height="8"><path d="M1 7l4-4M5 3a2 2 0 103-3" fill="none" stroke="#111" stroke-width="1.4"/></svg>SIM Lesemodul</div>
  <div class="info" style="top:382px">i</div>
  <div class="info" style="top:407px">i</div>
  <div class="info" style="top:432px">i</div>
  <div class="info" style="top:457px">i</div>
</section>

<!-- Danke -->
<section class="phone" style="left:1042px;top:585px">
  <header class="head">
    <div class="status"><span class="carrier">●●●●● Netz</span><span class="time">9:41 AM</span><span class="batt">100% <i></i></span></div>
    <svg class="back" width="8" height="12"><use href="#back"/></svg>
    <div class="brand">Flickwerkzentrale</div>
    <svg class="basket" width="14" height="14"><use href="#basket"/></svg>
  </header>
  <div class="center" style="top:82px;font-size:21px;font-weight:700">Vielen Dank!</div>
  <div class="center" style="top:144px;font-size:8.5px;font-weight:700;color:var(--green)">Geräteklinik.de</div>
  <div class="center" style="top:175px;font-size:8.5px;line-height:14px">Lindenallee 12<br>80331 Musterstadt</div>
  <div class="center" style="top:213px;font-size:8px;line-height:15px"><span class="phone-ico">✆</span>01234 - 5670 111<br><span class="phone-ico">✆</span>01234 - 5674 125</div>
  <div class="center" style="top:254px;font-size:8.5px;line-height:14px">Öffnungszeiten:<br>Mo-Fr. 9.00 Uhr - 18.00 Uhr<br>Sa. 10.00 Uhr - 15.00 Uhr</div>
  <div class="abs" style="left:0;right:0;top:325px;border-top:1px solid var(--line)"></div>
  <div class="row" style="top:325px"><span class="x" style="left:12px">✕</span><span class="name" style="left:32px">Bluetooth Antenne</span><span class="price">100 €</span></div>
  <div class="row" style="top:359px"><span class="x" style="left:12px">✕</span><span class="name" style="left:32px">SIM Lesemodul</span><span class="price">100 €</span></div>
  <div class="abs" style="left:200px;top:325px;width:1px;height:68px;background:var(--line)"></div>
  <div class="total" style="top:393px"><span style="margin-left:32px">Total</span><span class="abs" style="right:24px">200 €</span></div>
  <div class="btn" style="top:437px">BEZAHLEN</div>
</section>

</div>
</body>
</html>
```